Apparel store needs a cover for their seasonal catalogue

Every season the store creates a catalogue with a preview of the collection for the customers, the catalogue is printed and sent to 25 000 customers.We need a cover and back cover project for the upcoming winter season.Here is the current summer catalogue - https://www.la-botte.com/catalogue.shtmlFormat165mmx240mmAttached is some older issues, please note that the name LE SABOT MIRANVEL should be written on it as well as automne - hiver 2019 (fall-winter 19).

Target Market(s)

medium to high price consumers - male and female

Industry/Entity Type

Shoe Store

Colors

Designer to choose colors to be used in the design.

Requirements
Must have
• company name - LE SABOT MIRANVEL
• season - automne hiver 2019
• "Arty feel" to it
Nice to have
• Creative ideas - abstract themes
• As exemple I uploaded some older cover, but you do not have to follow the same patterns
Should not have
• product images

```html
<!DOCTYPE html>
<html lang="fr">
<head>
<meta charset="utf-8">
<title>Le Sabot Miranvel — Automne Hiver 2019</title>
<link rel="stylesheet" href="https://fonts.googleapis.com/css2?family=Libre+Baskerville:ital,wght@1,400;1,700&display=swap">
<style>
  :root {
    --paint-blue: #5b8fc8;
    --paint-ultramarine: #3f3fb8;
    --paint-peach: #f2c3ad;
    --paint-red: #e2545a;
    --paint-mint: #8fdcc2;
    --paint-white: #eef0ee;
    --band-white: #ffffff;
    --ink: #111111;
  }
  * { box-sizing: border-box; margin: 0; padding: 0; }
  html, body {
    width: 1200px;
    height: 753px;
    overflow: hidden;
    background: var(--band-white);
  }
  .cover {
    position: relative;
    width: 1200px;
    height: 753px;
    overflow: hidden;
  }
  .cover__artwork {
    position: absolute;
    inset: 0;
    background:
      radial-gradient(ellipse 260px 320px at 120px 200px, var(--paint-blue), transparent 70%),
      radial-gradient(ellipse 220px 300px at 470px 260px, var(--paint-ultramarine), transparent 70%),
      radial-gradient(ellipse 300px 220px at 800px 150px, var(--paint-red), transparent 70%),
      radial-gradient(ellipse 200px 260px at 1120px 320px, var(--paint-blue), transparent 70%),
      radial-gradient(ellipse 220px 160px at 1000px 420px, var(--paint-mint), transparent 70%),
      radial-gradient(ellipse 260px 200px at 660px 480px, var(--paint-peach), transparent 70%),
      linear-gradient(120deg, var(--paint-peach), var(--paint-white) 45%, var(--paint-peach) 70%, var(--paint-blue));
  }
  .cover__title-band {
    position: absolute;
    left: 0;
    top: 607px;
    width: 1200px;
    height: 113px;
    background: var(--band-white);
    display: flex;
    flex-direction: column;
    align-items: center;
    justify-content: center;
    color: var(--ink);
    font-family: "Libre Baskerville", Georgia, serif;
    font-style: italic;
  }
  .cover__brand {
    font-size: 38px;
    font-weight: 700;
    letter-spacing: 0.42em;
    margin-right: -0.42em;
    line-height: 1;
    margin-top: 4px;
  }
  .cover__season {
    font-size: 15px;
    font-weight: 400;
    letter-spacing: 0.38em;
    margin-right: -0.38em;
    line-height: 1;
    margin-top: 26px;
  }
</style>
</head>
<body>
  <main class="cover">
    <div class="cover__artwork" role="img" aria-label="Abstract palette-knife painting in blue, ultramarine, peach, red and mint with bare dark tree silhouettes"></div>
    <header class="cover__title-band">
      <h1 class="cover__brand">LE SABOT MIRANVEL</h1>
      <p class="cover__season">AUTOMNE HIVER 2019</p>
    </header>
  </main>
</body>
</html>
```